Luxury WordPress Website for CORALBASINS

I need a professional WordPress website for Coral Basins. The site should be modern, visually appealing, and user-friendly, reflecting the brand’s luxury and premium identity. It must include a homepage, product/service pages, contact form, and be responsive on both desktop and mobile devices. The design should allow for easy updates and integration of future content, while maintaining a polished and professional look.

Target Market(s)

swimmingpool & spa

Industry/Entity Type

Swimmingpool

Coding

Coded - Design and coding required

Font styles to use
Other font styles liked:
• HaboroSoft

Requirements
Must have
• Exclusive appearance
Nice to have
• • A logo that subtly incorporates water or pool elements. • A color palette that reflects luxury, elegance, and relaxation. • Clean and modern typography that is easy to read across all media. • Iconography or design elements that convey premium quality. • A versatile design that can be adapted for social media, merchandise, and promotional materials. • Optional: A tagline that emphasizes luxury and high-end pool experiences.

```html
<!DOCTYPE html>
<html lang="en">
<head>
<meta charset="utf-8">
<title>Coral Basins — Luxury Pools</title>
<link href="https://fonts.googleapis.com/css2?family=Outfit:wght@400;500;600&family=Josefin+Sans:wght@400;600&display=swap" rel="stylesheet">
<style>
:root{
  --navy:#0f1b2b;
  --accent:#4fa3d9;
  --sky:#eaf3fd;
  --cream:#f5f3ee;
  --text:#1c2530;
  --muted:#5a6470;
  --white:#fff;
  --line:#d8e4f0;
}
*{box-sizing:border-box;margin:0;padding:0}
html,body{width:1200px;height:4383px;overflow:hidden}
body{position:relative;background:var(--white);font-family:"Josefin Sans",sans-serif;color:var(--text)}
.abs{position:absolute}
.heading{position:absolute;left:0;width:1200px;text-align:center;font-family:"Outfit",sans-serif;font-weight:500;font-size:30px;letter-spacing:.5px;color:var(--navy)}
.rule{position:absolute;width:40px;height:2px;background:var(--accent)}
.btn{position:absolute;display:flex;align-items:center;justify-content:center;font-size:12.5px;letter-spacing:.4px;text-transform:uppercase;border-radius:4px}
.btn-dark{background:var(--navy);color:var(--white)}
.btn-light{background:var(--white);color:var(--navy);border:1.5px solid var(--navy)}
.photo{position:absolute;border-radius:10px}

/* header */
.site-header{position:absolute;left:0;top:0;width:1200px;height:80px;background:var(--cream);z-index:3}
.brand{position:absolute;left:105px;top:0;width:158px;height:117px;background:var(--white);z-index:4;display:flex;flex-direction:column;align-items:center;justify-content:center;gap:10px}
.brand-dot{width:30px;height:30px;border-radius:50%;background:var(--navy)}
.brand-name{font-family:"Josefin Sans",sans-serif;font-weight:600;font-size:17px;line-height:20px;text-align:center;color:var(--navy);letter-spacing:1px}
.nav a{position:absolute;top:36px;font-size:13px;letter-spacing:.4px;color:#3b4550;text-decoration:none}
.nav a.active{color:var(--accent)}

/* hero */
.hero-photo{position:absolute;left:0;top:80px;width:1200px;height:490px;background:linear-gradient(180deg,#5d7480 0%,#7fa7b5 30%,#3f9bcf 55%,#1f7fbf 100%)}
.hero-title{position:absolute;left:0;top:248px;width:1200px;text-align:center;font-family:"Outfit",sans-serif;font-weight:500;font-size:32px;color:var(--white);z-index:2}

/* about */
.about-text{position:absolute;left:641px;top:740px;width:440px;font-size:15.5px;line-height:34.5px;color:var(--text)}
.about-text p+p{margin-top:12px}

/* services */
.services-bg{position:absolute;left:0;top:1202px;width:1200px;height:738px;background:var(--sky);border-radius:60px 60px 0 0}
.svc-card{position:absolute;top:1361px;width:310px;height:404px;background:var(--white);border-radius:14px;box-shadow:0 4px 16px rgba(20,50,90,.08);text-align:center}
.svc-card .photo{left:13px;top:14px;width:284px;height:205px}
.svc-title{position:absolute;left:0;top:250px;width:100%;font-size:16px;letter-spacing:.4px;color:var(--navy)}
.svc-desc{position:absolute;left:20px;top:286px;width:270px;font-size:13.5px;line-height:34px;color:var(--text)}
.svc-icon{position:absolute;left:122px;top:372px;width:66px;height:66px;border-radius:50%;background:var(--white);border:1.5px solid var(--line);display:flex;align-items:center;justify-content:center}
.arrow{position:absolute;width:30px;height:30px;border-radius:50%;border:1.5px solid var(--navy);display:flex;align-items:center;justify-content:center}

/* testimonials */
.review-card{position:absolute;left:112px;top:2195px;width:558px;height:267px;background:var(--white);border-radius:14px;box-shadow:0 4px 22px rgba(20,50,90,.12)}
.quote-badge{position:absolute;left:500px;top:2162px;width:60px;height:60px;background:var(--accent);border-radius:8px;color:var(--white);font-family:"Outfit",sans-serif;font-size:58px;line-height:80px;text-align:center;z-index:2}
.dots{position:absolute;top:2440px;left:868px;display:flex;gap:18px;align-items:center}
.dots span{width:7px;height:7px;border-radius:50%;background:var(--navy)}

/* why */
.why-bg{position:absolute;left:0;top:3357px;width:1200px;height:640px;background:var(--sky);border-radius:60px 60px 0 0}
.why-card{position:absolute;top:3524px;width:220px;height:226px;background:var(--white);border:1.5px solid var(--line);border-radius:40px 10px 40px 10px;text-align:center;font-size:14.5px;line-height:33px;letter-spacing:.4px;color:var(--navy)}
.why-card.active{background:var(--navy);color:var(--white);border-color:var(--navy)}
.why-card svg{position:absolute;left:80px;top:42px}
.why-card .label{position:absolute;left:0;width:100%;top:128px}

/* footer */
.footer{position:absolute;left:0;top:3990px;width:1200px;height:393px;background:var(--navy)}
.footer h4{position:absolute;top:75px;font-weight:400;font-size:16px;letter-spacing:.5px;color:var(--accent)}
.footer .link{position:absolute;left:516px;font-size:14px;color:var(--white)}
.footer .contact{position:absolute;left:864px;font-size:14px;line-height:30px;color:var(--white)}
.footer .icon{position:absolute;left:809px;width:36px;height:36px;border-radius:50%;border:1.5px solid var(--accent);display:flex;align-items:center;justify-content:center}
.footer-brand{position:absolute;left:110px;top:90px;width:246px;text-align:center;color:var(--white);font-weight:600;font-size:36px;line-height:40px;letter-spacing:2px}
.footer-brand .brand-dot{margin:0 auto 20px;width:50px;height:50px;background:var(--white)}
.copyright{position:absolute;left:0;top:368px;width:1200px;text-align:center;font-size:11.5px;color:var(--white);letter-spacing:.4px}
</style>
</head>
<body>

<!-- Header -->
<header class="site-header">
  <nav class="nav">
    <a class="active" style="left:448px">HOME</a>
    <a style="left:527px">ABOUT US</a>
    <a style="left:636px">OUR SERVICES</a>
    <a style="left:774px">CONTACT US</a>
  </nav>
  <div class="btn btn-dark" style="left:910px;top:22px;width:178px;height:38px;font-size:12px">Book a consultation</div>
</header>
<div class="brand">
  <div class="brand-dot"></div>
  <div class="brand-name">CORAL<br>BASINS</div>
</div>

<!-- Hero -->
<div class="hero-photo" role="img" aria-label="Modern villa beside a long blue lap pool with two loungers on the deck"></div>
<svg class="abs" style="left:0;top:400px;z-index:1" width="1200" height="180" viewBox="0 0 1200 180">
  <path d="M0 60 C200 170 420 190 620 140 C820 90 1000 30 1200 50 L1200 180 L0 180Z" fill="#fff"/>
  <path d="M0 60 C200 170 420 190 620 140 C820 90 1000 30 1200 50" fill="none" stroke="#4fa3d9" stroke-width="6"/>
</svg>
<h1 class="hero-title">CRAFTED FOR PERFECTION. DESIGNED FOR LIFE.</h1>
<div class="btn" style="left:505px;top:327px;width:189px;height:40px;background:#fff;color:var(--navy);z-index:2">Start your journey</div>

<!-- About -->
<h2 class="heading" style="top:638px">ABOUT CORAL BASINS</h2>
<div class="rule" style="left:580px;top:690px"></div>
<svg class="abs" style="left:110px;top:735px" width="470" height="400">
  <circle cx="230" cy="200" r="190" fill="none" stroke="#9cc6e6" stroke-width="1.4" stroke-dasharray="4 4"/>
  <circle cx="200" cy="185" r="80" fill="#d8dde3"/>
</svg>
<div class="photo" style="left:110px;top:758px;width:200px;height:200px;border-radius:50%;background:radial-gradient(circle,#5bc0e6,#1c8cc6)" role="img" aria-label="Swimmer in a sun hat resting at the pool edge"></div>
<div class="photo" style="left:322px;top:740px;width:97px;height:97px;border-radius:50%;background:linear-gradient(180deg,#9fc7e3,#3a8fc4)" role="img" aria-label="Infinity pool overlooking the ocean"></div>
<div class="photo" style="left:320px;top:845px;width:250px;height:250px;border-radius:50%;background:linear-gradient(180deg,#3f6b48 0%,#6b8a6a 45%,#2a9ad6 70%,#1a77b8 100%)" role="img" aria-label="Backyard pool with pavilion and pine trees"></div>
<div class="photo" style="left:165px;top:977px;width:152px;height:152px;border-radius:50%;background:radial-gradient(circle,#a6e1ea,#46b3cf)" role="img" aria-label="Swimmer floating in turquoise water from above"></div>
<div class="about-text">
  <p>At Coral Basins, we craft more than just pools—we create luxurious outdoor experiences that elevate your lifestyle. Every pool we design and build is a testament to our commitment to exquisite design, exceptional durability, and unparalleled attention to detail.</p>
  <p>With years of expertise in the pool industry, our team blends cutting-edge technology, premium materials, and bespoke design solutions to bring your vision to life. Whether it’s a sleek infinity pool, a serene lap pool, or a custom family</p>
</div>
<div class="btn btn-dark" style="left:641px;top:1083px;width:117px;height:36px;font-size:11.5px">Learn more</div>

<!-- Services -->
<div class="services-bg"></div>
<h2 class="heading" style="top:1258px">CORAL BASINS SERVICES</h2>
<div class="rule" style="left:580px;top:1310px"></div>

<div class="arrow" style="left:31px;top:1462px"><svg width="10" height="12"><path d="M7 1L2 6l5 5" fill="none" stroke="#0f1b2b" stroke-width="1.6"/></svg></div>
<div class="arrow" style="left:1122px;top:1462px;border-color:var(--accent)"><svg width="10" height="12"><path d="M3 1l5 5-5 5" fill="none" stroke="#4fa3d9" stroke-width="1.6"/></svg></div>

<article class="svc-card" style="left:110px">
  <div class="photo" style="background:linear-gradient(180deg,#8d9aa3,#7c8c70 45%,#3aa6d6 75%,#2b7db8)" role="img" aria-label="Custom villa pool and spa from above"></div>
  <div class="svc-title">CUSTOM POOL DESIGN</div>
  <div class="svc-desc">Every home is unique, and so is every pool we create. From concept to</div>
  <div class="svc-icon"><svg width="30" height="26" fill="none" stroke="#4fa3d9" stroke-width="1.5"><path d="M2 22q4-3 8 0t8 0 8 0"/><path d="M8 18V4h6v14M8 9h6"/><circle cx="21" cy="6" r="3"/></svg></div>
</article>
<article class="svc-card" style="left:446px">
  <div class="photo" style="background:linear-gradient(180deg,#7fb8d8,#b8d9e6 45%,#5aa7cf 60%,#3d8fc2)" role="img" aria-label="Person at the edge of an infinity pool facing the sea"></div>
  <div class="svc-title">INFINITY &amp; LAP POOLS</div>
  <div class="svc-desc">Experience elegance and sophistication with our infinity and</div>
  <div class="svc-icon"><svg width="30" height="26" fill="none" stroke="#4fa3d9" stroke-width="1.5"><path d="M2 22q4-3 8 0t8 0 8 0"/><path d="M2 17q4-3 8 0t8 0 8 0"/><circle cx="17" cy="7" r="3"/><path d="M8 14l6-4 4 3"/></svg></div>
</article>
<article class="svc-card" style="left:780px">
  <div class="photo" style="background:linear-gradient(180deg,#3b6b3a,#4c7d45 40%,#1f95e0 55%,#1a7fd0)" role="img" aria-label="Technician cleaning a pool lined with trees"></div>
  <div class="svc-title">MAINTENANCE &amp; SUPPORT</div>
  <div class="svc-desc">Enjoy your pool without the hassle. Our professional maintenance</div>
  <div class="svc-icon"><svg width="28" height="30" fill="none" stroke="#4fa3d9" stroke-width="1.5"><rect x="3" y="4" width="18" height="24" rx="2"/><path d="M9 2h6v4H9zM7 12h10M7 17h6"/><circle cx="20" cy="22" r="5"/></svg></div>
</article>

<div class="btn btn-dark" style="left:380px;top:1845px;width:190px;height:41px">Explore our pools</div>
<div class="btn btn-light" style="left:595px;top:1845px;width:225px;height:41px">Request a consultation</div>

<!-- Testimonials -->
<h2 class="abs" style="left:111px;top:2016px;font-family:Outfit,sans-serif;font-weight:500;font-size:30px;color:var(--navy)">WHAT OUR CUSTOMERS SAY</h2>
<div class="rule" style="left:112px;top:2074px"></div>
<div class="abs" style="left:114px;top:2105px;font-size:16px;color:var(--navy)"><span style="color:#4a7fd8">Verified</span> <b style="font-weight:600">Reviews</b></div>
<div class="abs" style="left:114px;top:2135px;font-size:16px;font-weight:600;color:var(--navy)">4.4 <span style="color:#e9b024;letter-spacing:1px">★★★★★</span> <span style="font-size:11px;font-weight:400;color:#999">(97)</span></div>
<div class="quote-badge">”</div>
<div class="review-card">
  <div class="abs" style="left:38px;top:30px;color:#e9b024;font-size:20px;letter-spacing:1px">★★★★★</div>
  <div class="abs" style="left:38px;top:80px;width:480px;font-size:14.5px;line-height:36px">“Coral Basins transformed our backyard into a stunning retreat.<br>The craftsmanship and attention to detail are truly unmatched.”</div>
  <div class="abs" style="left:38px;top:170px;width:63px;height:63px;border-radius:50%;background:linear-gradient(180deg,#c9c1b8,#8e8278)" role="img" aria-label="Customer portrait"></div>
  <div class="abs" style="left:131px;top:182px;font-size:13px;color:var(--accent)">CLARA M.</div>
  <div class="abs" style="left:131px;top:213px;font-size:13px;color:var(--navy)">HOMEOWNER</div>
  <svg class="abs" style="left:513px;top:212px" width="24" height="24"><circle cx="12" cy="12" r="10" fill="none" stroke="#4a7fd8" stroke-width="3"/></svg>
</div>
<div class="photo" style="left:603px;top:2023px;width:489px;height:380px;border-radius:14px;background:linear-gradient(180deg,#3f5b34,#7b8e6b 40%,#4fb0e3 60%,#2b8fd0)" role="img" aria-label="Resort pool with loungers and tropical plants"></div>
<div class="dots">
  <svg width="10" height="14"><path d="M7 2L2 7l5 5" fill="none" stroke="#0f1b2b" stroke-width="1.6"/></svg>
  <span style="width:11px;height:11px;background:#fff;border:3px solid var(--accent)"></span><span></span><span></span><span></span>
  <svg width="10" height="14"><path d="M3 2l5 5-5 5" fill="none" stroke="#0f1b2b" stroke-width="1.6"/></svg>
</div>

<!-- Portfolio -->
<h2 class="heading" style="top:2542px">CORAL BASINS PORTFOLIO</h2>
<div class="rule" style="left:580px;top:2594px"></div>
<div class="photo" style="left:110px;top:2645px;width:233px;height:163px;border-radius:8px;background:linear-gradient(135deg,#8fd0d4,#5ab3bb)" role="img" aria-label="Swimmer in a turquoise pool from above"></div>
<div class="photo" style="left:110px;top:2820px;width:233px;height:163px;border-radius:8px;background:linear-gradient(180deg,#7aa7d9,#6f7c5a 45%,#36a6d8 75%)" role="img" aria-label="Pool in front of a pavilion"></div>
<div class="photo" style="left:110px;top:3000px;width:233px;height:186px;border-radius:8px;background:linear-gradient(180deg,#36b1e3,#1d88c6)" role="img" aria-label="Swimmer in a sun hat at the pool"></div>
<div class="photo" style="left:359px;top:2645px;width:233px;height:245px;border-radius:8px;background:linear-gradient(180deg,#2a7fd0,#9fd0ea 45%,#e0e0dc 65%,#8b8b86)" role="img" aria-label="Towel on a striped lounger by the sea"></div>
<div class="photo" style="left:359px;top:2903px;width:233px;height:283px;border-radius:8px;background:radial-gradient(circle,#8fe0ee,#2fa4d6)" role="img" aria-label="Child swimming underwater with goggles"></div>
<div class="photo" style="left:608px;top:2645px;width:233px;height:205px;border-radius:8px;background:linear-gradient(180deg,#c9d6e2,#3e6b40 45%,#4ab3dd 75%,#c8c8c4)" role="img" aria-label="Pool terrace with loungers and trees"></div>
<div class="photo" style="left:608px;top:2864px;width:233px;height:244px;border-radius:8px;background:radial-gradient(circle,#f07bc8,#3ed0e8 55%,#23b4dc)" role="img" aria-label="Child on a pink float in a pool"></div>
<div class="photo" style="left:608px;top:3120px;width:233px;height:66px;border-radius:8px 8px 0 0;background:linear-gradient(90deg,#c8a072,#6fb5dd)" role="img" aria-label="Drinks beside a pool edge"></div>
<div class="photo" style="left:857px;top:2645px;width:233px;height:165px;border-radius:8px;background:radial-gradient(circle,#4fcaf0,#1d9fe0)" role="img" aria-label="Swimmer underwater in blue pool"></div>
<div class="photo" style="left:857px;top:2824px;width:233px;height:214px;border-radius:8px;background:linear-gradient(180deg,#e6eef4,#8cc6e8 50%,#2d8cc8)" role="img" aria-label="Infinity pool meeting the horizon"></div>
<div class="photo" style="left:857px;top:3052px;width:233px;height:134px;border-radius:8px;background:linear-gradient(180deg,#8aa0a8,#2fa3c9 30%,#3bbcd2)" role="img" aria-label="Rectangular pool from above"></div>
<div class="btn btn-dark" style="left:506px;top:3230px;width:189px;height:40px">View our portfolio</div>

<!-- Why choose -->
<div class="why-bg"></div>
<h2 class="heading" style="top:3410px">WHY CHOOSE US</h2>
<div class="rule" style="left:580px;top:3462px"></div>

<div class="why-card" style="left:110px">
  <svg width="60" height="60" fill="none" stroke="#4fa3d9" stroke-width="1.6"><circle cx="24" cy="26" r="18" fill="#e3ecf4" stroke="none"/><path d="M20 48V30l4-14 3 14h8l-3 18"/><path d="M40 20l4 4M44 14v4"/></svg>
  <div class="label">UNMATCHED<br>CRAFTSMANSHIP</div>
</div>
<div class="why-card active" style="left:363px">
  <svg width="60" height="60" fill="none" stroke="#fff" stroke-width="1.6"><circle cx="24" cy="26" r="18" fill="#24324a" stroke="none"/><path d="M24 12a12 12 0 0 0-7 21v6h14v-6a12 12 0 0 0-7-21zM19 44h10"/><circle cx="42" cy="18" r="6"/></svg>
  <div class="label">INNOVATIVE<br>TECHNOLOGY</div>
</div>
<div class="why-card" style="left:615px">
  <svg width="60" height="60" fill="none" stroke="#4fa3d9" stroke-width="1.6"><circle cx="24" cy="26" r="18" fill="#e3ecf4" stroke="none"/><circle cx="30" cy="30" r="18"/><circle cx="30" cy="26" r="6"/><path d="M20 42a10 10 0 0 1 20 0"/></svg>
  <div class="label">PERSONALIZED<br>SERVICE</div>
</div>
<div class="why-card" style="left:868px">
  <svg width="60" height="60" fill="none" stroke="#4fa3d9" stroke-width="1.6"><circle cx="24" cy="26" r="18" fill="#e3ecf4" stroke="none"/><rect x="20" y="12" width="20" height="34" rx="2"/><path d="M25 20h10M25 27h10M25 34h6M46 14v30"/></svg>
  <div class="label" style="top:140px">BESPOKE DESIGNS</div>
</div>
<div class="btn btn-dark" style="left:532px;top:3800px;width:136px;height:40px">Learn more</div>

<!-- Footer wave -->
<svg class="abs" style="left:0;top:3870px;z-index:1" width="1200" height="130" viewBox="0 0 1200 130">
  <path d="M0 130 L0 120 C200 100 420 40 640 20 C860 0 1040 40 1200 120 L1200 130Z" fill="#0f1b2b"/>
  <path d="M0 120 C200 100 420 40 640 20 C860 0 1040 40 1200 120" fill="none" stroke="#4fa3d9" stroke-width="6"/>
</svg>

<footer class="footer">
  <div class="footer-brand"><div class="brand-dot"></div>CORAL<br>BASINS</div>
  <h4 style="left:516px">QUICK LINKS</h4>
  <div class="link" style="top:120px">Home</div>
  <div class="link" style="top:161px">About Us</div>
  <div class="link" style="top:202px">Services / Pools</div>
  <div class="link" style="top:243px">Projects / Gallery</div>
  <div class="link" style="top:284px">Contact Us</div>

  <h4 style="left:809px">CONTACT US</h4>
  <div class="icon" style="top:115px"><svg width="16" height="16" fill="none" stroke="#4fa3d9" stroke-width="1.5"><path d="M3 2l3 0 1.5 4-2 1.5a9 9 0 0 0 3 3L10 8.5l4 1.5v3a1.5 1.5 0 0 1-1.5 1.5A12 12 0 0 1 1.5 3.5 1.5 1.5 0 0 1 3 2z"/></svg></div>
  <div class="contact" style="top:118px">+1 (555) 018-2290</div>
  <div class="icon" style="top:184px"><svg width="16" height="14" fill="none" stroke="#4fa3d9" stroke-width="1.5"><rect x="1" y="2" width="14" height="10" rx="1"/><path d="M1 3l7 5 7-5"/></svg></div>
  <div class="contact" style="top:187px">hello@coralbasins.com</div>
  <div class="icon" style="top:260px"><svg width="14" height="18" fill="none" stroke="#4fa3d9" stroke-width="1.5"><path d="M7 17s-6-6-6-10a6 6 0 0 1 12 0c0 4-6 10-6 10z"/><circle cx="7" cy="7" r="2"/></svg></div>
  <div class="contact" style="top:245px">48 Coral Way, Harbor City,<br>CA 90211</div>

  <div class="copyright">© 2025 CORAL BASINS. ALL RIGHTS RESERVED.</div>
</footer>

</body>
</html>
```